Brindlewick Solutions Ltd

I'd like to create a company letterhead for the attached logo in word format.

I'd like to emphasis the icon in large translucent state from the left corner and ensure that the letterhead colouring matches the colour palette of the current logo with a contrast so it's clear to see. I've attached a copy of our sister company page on the app for reference.

```html
<!DOCTYPE html>
<html lang="en">
<head>
<meta charset="utf-8">
<title>Brindlewick Solutions Ltd – Letterhead</title>
<link rel="stylesheet" href="https://fonts.googleapis.com/css2?family=Open+Sans:wght@400;600&display=swap">
<style>
  :root {
    --backdrop: #e4e4e4;
    --paper: #ffffff;
    --teal: #2fae9f;
    --swoosh-grey: #d4d5d6;
    --swoosh-pale: #eeeff0;
    --watermark: #f2f3f3;
    --ink-grey: #8a8d8f;
  }
  * { box-sizing: border-box; margin: 0; padding: 0; }
  html, body {
    width: 1200px;
    height: 800px;
    overflow: hidden;
    background: var(--backdrop);
    font-family: "Open Sans", Arial, sans-serif;
  }
  .canvas {
    width: 1200px;
    height: 800px;
    display: flex;
    align-items: center;
    justify-content: center;
  }
  .letterhead {
    position: relative;
    width: 510px;
    height: 720px;
    background: var(--paper);
    overflow: hidden;
    box-shadow: 0 2px 10px rgba(0, 0, 0, 0.08);
  }
  .letterhead-shapes {
    position: absolute;
    inset: 0;
    width: 510px;
    height: 720px;
  }
  .brand {
    position: absolute;
    left: 26px;
    top: 62px;
    display: flex;
    align-items: center;
    gap: 8px;
    color: var(--teal);
    font-weight: 600;
  }
  .brand-dot {
    width: 30px;
    height: 30px;
    border-radius: 50%;
    background: var(--teal);
    flex: none;
  }
  .brand-name {
    font-size: 21px;
    line-height: 1;
  }
  .brand-tagline {
    display: block;
    font-size: 7.5px;
    letter-spacing: 3.2px;
    text-transform: uppercase;
    margin-top: 3px;
  }
  .contact {
    position: absolute;
    right: 30px;
    top: 26px;
    width: 150px;
    font-size: 8px;
    line-height: 1.45;
    color: var(--ink-grey);
  }
  .contact-line {
    display: flex;
    align-items: center;
    gap: 5px;
  }
  .contact-icon {
    width: 9px;
    height: 9px;
    flex: none;
  }
  .website {
    position: absolute;
    right: 22px;
    bottom: 20px;
    font-size: 10px;
    color: var(--paper);
    letter-spacing: 0.2px;
  }
</style>
</head>
<body>
<main class="canvas">
  <article class="letterhead">
    <svg class="letterhead-shapes" viewBox="0 0 510 720" aria-hidden="true">
      <!-- faint corner watermark circle -->
      <circle cx="140" cy="720" r="270" fill="var(--watermark)"/>
      <circle cx="140" cy="720" r="190" fill="var(--paper)" opacity="0.55"/>
      <!-- header swoosh -->
      <path d="M0,0 H300 A310 310 0 0 1 0,200 Z" fill="var(--swoosh-pale)"/>
      <path d="M270,0 H300 A310 310 0 0 1 0,200 V178 A285 285 0 0 0 270,0 Z" fill="var(--swoosh-grey)"/>
      <!-- footer bands -->
      <path d="M160,720 Q300,618 510,628 V652 Q320,646 200,720 Z" fill="var(--swoosh-grey)"/>
      <path d="M200,720 Q320,646 510,652 V720 Z" fill="var(--teal)"/>
    </svg>

    <header class="brand">
      <span class="brand-dot"></span>
      <span>
        <span class="brand-name">Brindlewick</span>
        <span class="brand-tagline">Solutions Ltd</span>
      </span>
    </header>

    <address class="contact" style="font-style: normal;">
      <div>Suite 214 Mill Lane,</div>
      <div>State, Zip 4410, Country</div>
      <div class="contact-line">
        <svg class="contact-icon" viewBox="0 0 10 10"><circle cx="5" cy="5" r="5" fill="var(--teal)"/><path d="M3.2,2.6 l1,1 -0.5,0.6 q0.6,1.2 1.8,1.8 l0.6,-0.5 1,1 -0.7,0.8 q-2.6,-0.6 -3.9,-3.9z" fill="#fff"/></svg>
        <span>(00) 01234 567 321</span>
      </div>
      <div class="contact-line">
        <svg class="contact-icon" viewBox="0 0 10 10"><circle cx="5" cy="5" r="5" fill="var(--teal)"/><rect x="2.4" y="3.2" width="5.2" height="3.6" fill="#fff"/><path d="M2.4,3.2 L5,5.2 L7.6,3.2" fill="none" stroke="var(--teal)" stroke-width="0.6"/></svg>
        <span>hello@brindlewick.com</span>
      </div>
    </address>

    <footer class="website">www.brindlewicksolutions.com</footer>
  </article>
</main>
</body>
</html>
```